Website for IT consulting Company

I need a website upgrade, the existing site content is ok, I would also like to add a testimonial page, the site should be something that is easy for us to update content. You use the content from www.kelvanbrook.com as an example. I will also post update logo and artwork. I also need a contact form with some type of validation or captcha.

I added Coded to the Project

Please omit Address maps

Target Market(s)

small business, service oriented companies. We provide IT Consulting, support and mangement

Industry/Entity Type

Information Technology

Coding

Number of Pages Required

1 page

Font styles to use
Serif
Sans Serif

Requirements
Must have
• Contain logo attached, and content from existing web site www.kelvanbrook.com.
• Also need to update content easily, and be movable to different platforms.
• There is a catch phrase
• "Let us worry about your technology…” “ so you don’t have to!”
• Should be included.
Nice to have
• Testimonial page, Project page where we can post new and past projects and pictures
Should not have
• none

```html
<!DOCTYPE html>
<html lang="en">
<head>
<meta charset="utf-8">
<title>Kelvanbrook Development Group</title>
<link href="https://fonts.googleapis.com/css2?family=Exo+2:ital,wght@0,600;0,700;1,600;1,700;1,800&family=Open+Sans:ital,wght@0,400;0,600;0,700;1,400&family=PT+Serif&display=swap" rel="stylesheet">
<style>
:root{
  --blue:#1b93dc;
  --blue-deep:#0f6fb8;
  --blue-light:#3fb0ee;
  --ink:#222;
  --text:#333;
  --muted:#666;
  --dark:#2a2a2a;
  --gray-bg:#e6e6e6;
  --field:#fff;
  --line:#cfcfcf;
  --white:#fff;
}
*{box-sizing:border-box;margin:0;padding:0}
html,body{width:1200px;height:2927px;overflow:hidden}
body{position:relative;background:var(--white);font-family:"Open Sans",Arial,sans-serif;color:var(--text)}
.abs{position:absolute}

/* top bar */
.topbar{left:0;top:0;width:1200px;height:35px;background:var(--dark)}
.topbar .social{position:absolute;right:30px;top:5px;display:flex;gap:8px}
.topbar .social span{width:26px;height:26px;background:#9a9a9a;border-radius:2px}

/* header */
.header{left:0;top:35px;width:1200px;height:88px;background:var(--white)}
.brand{position:absolute;left:80px;top:20px;display:flex;align-items:center;gap:12px}
.brand-mark{width:44px;height:44px;background:var(--blue);border-radius:6px}
.brand-name{font-family:"Exo 2",sans-serif;font-weight:700;font-size:36px;color:#555;line-height:1}
.brand-tag{position:absolute;left:136px;top:62px;font-size:10px;font-style:italic;color:var(--blue)}
.header-phone{position:absolute;right:58px;top:32px;display:flex;align-items:center;gap:14px;font-family:"Exo 2",sans-serif;font-style:italic;font-weight:700;font-size:20px;color:#444}
.phone-badge{width:28px;height:28px;background:var(--blue-deep);border-radius:3px;display:flex;align-items:center;justify-content:center}

/* nav */
.nav{left:0;top:123px;width:1200px;height:58px;background:linear-gradient(#3aa6e8,#1583cc);display:flex;align-items:center;padding-left:98px}
.nav a{font-family:"Exo 2",sans-serif;font-style:italic;font-weight:700;font-size:18px;color:var(--white);text-decoration:none;margin-right:70px;letter-spacing:.5px}
.nav a.active{color:#0b3f6a;text-decoration:underline;text-underline-offset:5px}

/* hero */
.hero{left:0;top:181px;width:1200px;height:533px;background:radial-gradient(ellipse at 68% 45%,#5fb8f0 0%,#1f6fae 22%,#0c2e4e 55%,#06121f 100%)}
.hero-title{position:absolute;left:84px;top:195px;font-family:"Exo 2",sans-serif;font-style:italic;font-weight:700;font-size:34px;line-height:49px;color:var(--white)}
.hero-title .accent{color:var(--blue-light)}
.hero-dots{position:absolute;left:88px;top:352px;display:flex;gap:5px}
.hero-dots span{width:10px;height:8px;background:#888}
.hero-dots span.on{background:#fff}

/* welcome */
.welcome{left:84px;top:768px;width:640px}
.section-title{font-family:"Exo 2",sans-serif;font-style:italic;font-weight:700;font-size:26px;color:var(--ink);letter-spacing:.5px;white-space:nowrap}
.section-title .accent{color:var(--blue)}
.welcome .section-title{font-size:24px;letter-spacing:.2px}
.welcome .rule{width:290px;height:2px;background:var(--ink);margin:6px 0 22px}
.welcome p{font-size:13.3px;line-height:22.5px;color:var(--text);margin-bottom:10px}

.inquiry{left:765px;top:761px;width:353px;height:324px;background:#ececec;border:1px solid #dcdcdc}
.inquiry-tab{position:absolute;left:47px;top:-12px;width:265px;height:41px;background:linear-gradient(#a3a3a3,#7a7a7a);color:var(--white);font-family:"Exo 2",sans-serif;font-style:italic;font-weight:700;font-size:20px;text-align:center;line-height:41px}
.field{position:absolute;left:20px;width:312px;height:35px;background:var(--field);border:1px solid var(--line);font-size:11px;color:#777;padding:10px}
.field.tall{height:78px}
.submit{position:absolute;left:27px;top:271px;width:123px;height:36px;background:linear-gradient(#3aa6e8,#1583cc);color:var(--white);font-family:"Exo 2",sans-serif;font-style:italic;font-weight:700;font-size:18px;text-align:center;line-height:36px}

/* services */
.services{left:0;top:1141px;width:1200px;height:572px;background:var(--gray-bg)}
.services .section-title{position:absolute;top:42px;width:1200px;text-align:center}
.services .rule{position:absolute;left:560px;top:84px;width:80px;height:2px;background:var(--blue)}
.services-art{position:absolute;left:228px;top:200px;width:744px;height:372px;border-radius:372px 372px 0 0;background:radial-gradient(ellipse at 50% 100%,#ffffff 0%,#f4f4f4 55%,#dcdcdc 100%)}
.services-name{position:absolute;left:0;top:498px;width:1200px;text-align:center;font-family:"Exo 2",sans-serif;font-weight:700;font-size:34px;color:#666}
.svc-label{position:absolute;font-family:"Exo 2",sans-serif;font-style:italic;font-weight:700;font-size:15px;color:#333;line-height:17px}

/* split panels */
.panel{top:1713px;width:605px;height:388px}
.panel.left{left:0;background:linear-gradient(#38a7ea,#1278c2)}
.panel.right{left:605px;width:595px;background:linear-gradient(#c9c9c9,#7d7d7d)}
.panel-notch{left:582px;top:1713px;width:0;height:0;border-left:23px solid transparent;border-right:23px solid transparent;border-top:24px solid var(--white)}
.panel-title{position:absolute;top:62px;display:flex;align-items:center;gap:12px;font-family:"Exo 2",sans-serif;font-style:italic;font-weight:700;font-size:23px;white-space:nowrap}
.panel.left .panel-title{left:86px;color:var(--white)}
.panel.right .panel-title{left:31px;color:var(--ink)}
.panel-rule{position:absolute;top:104px;width:60px;height:2px;background:rgba(255,255,255,.7)}
.panel-photo{position:absolute;top:131px;width:203px;height:185px;border:4px solid rgba(255,255,255,.25)}
.panel-text{position:absolute;top:126px;width:280px;font-size:13.3px;line-height:24.5px;color:var(--white)}
.read-more{position:absolute;top:279px;width:152px;height:39px;font-family:"PT Serif",Georgia,serif;font-size:16px;color:var(--white);line-height:39px;text-align:center}
.panel.left .read-more{left:310px;background:linear-gradient(#b6b6b6,#8c8c8c)}
.panel.right .read-more{left:253px;background:linear-gradient(#3aa6e8,#1583cc)}

/* testimonials */
.testimonials{left:0;top:2101px;width:1200px;height:354px;background:var(--white)}
.testimonials .section-title{position:absolute;top:52px;width:1200px;text-align:center}
.testimonials .rule{position:absolute;left:560px;top:94px;width:80px;height:2px;background:var(--blue)}
.quote{position:absolute;left:200px;top:140px;width:800px;text-align:center;font-style:italic;font-size:14.5px;line-height:31px;color:#333}
.quote .mark{font-family:"PT Serif",serif;font-size:34px;color:#aaa;line-height:0;vertical-align:-10px}
.author{position:absolute;top:258px;width:1200px;text-align:center;font-weight:700;font-size:15px;color:#222;line-height:24px}
.author small{display:block;font-size:14px}

/* cta */
.cta{left:0;top:2455px;width:1200px;height:101px;background:linear-gradient(#3aa6e8,#1583cc)}
.cta-text{position:absolute;left:84px;top:14px;font-family:"Exo 2",sans-serif;font-style:italic;font-weight:700;color:var(--white);font-size:33px;line-height:40px}
.cta-text .sub{font-size:27px;display:block;line-height:36px}
.call-btn{position:absolute;left:853px;top:23px;width:210px;height:53px;background:linear-gradient(#a8a8a8,#6f6f6f);border-radius:10px;display:flex;align-items:center;gap:10px;padding-left:12px;color:var(--white);font-family:"Exo 2",sans-serif;font-style:italic;font-weight:700;font-size:17px;line-height:19px}

/* footer */
.footer{left:0;top:2556px;width:1200px;height:326px;background:linear-gradient(180deg,#3a3f46 0%,#26292d 60%,#1b1c1e 100%)}
.footer-col{position:absolute;top:56px}
.footer-col h4{font-family:"Exo 2",sans-serif;font-style:italic;font-weight:700;font-size:18px;color:var(--white);margin-bottom:12px}
.footer-col h4 span{color:var(--blue)}
.footer-col ul{list-style:none}
.footer-col li{font-size:13px;color:#e4e4e4;line-height:25px}
.links li::before{content:"›";color:var(--blue);margin-right:12px}
.contact li{display:flex;align-items:center;gap:12px}
.contact .addr{line-height:20px;margin:6px 0 10px}
.social-list li{display:flex;align-items:center;gap:14px;height:44px}
.social-list .box{width:28px;height:28px;background:#d8d8d8;border-radius:2px}

.copyright{left:0;top:2882px;width:1200px;height:45px;background:linear-gradient(#2a9be2,#1479c4);color:var(--white);font-size:14px;font-weight:700;text-align:center;line-height:45px}
</style>
</head>
<body>

<div class="abs topbar">
  <div class="social"><span></span><span></span><span></span><span></span></div>
</div>

<header class="abs header">
  <div class="brand"><div class="brand-mark"></div><div class="brand-name">KELVANBROOK</div></div>
  <div class="brand-tag">Let us worry about your technology… So you don't have to!</div>
  <div class="header-phone">
    <span class="phone-badge"><svg width="16" height="16" viewBox="0 0 24 24"><path fill="#fff" d="M6.6 10.8a15.1 15.1 0 0 0 6.6 6.6l2.2-2.2c.3-.3.7-.4 1-.2 1.1.4 2.3.6 3.6.6.6 0 1 .4 1 1V20c0 .6-.4 1-1 1A17 17 0 0 1 3 4c0-.6.4-1 1-1h3.5c.6 0 1 .4 1 1 0 1.3.2 2.5.6 3.6.1.3 0 .7-.2 1z"/></svg></span>
    (555) 014-2870
  </div>
</header>

<nav class="abs nav">
  <a class="active">HOME</a><a>ABOUT US</a><a>SERVICES</a><a>SUPPORT</a><a>CLIENTS</a><a>CAREERS</a><a>CONTACT &nbsp;US</a>
</nav>

<section class="abs hero" role="img" aria-label="Hand holding a glowing laptop surrounded by a network of connected icons and a world map">
  <h1 class="hero-title">Let Us Worry About<br>Your Technology...<br><span class="accent">So You Don't Have To!</span></h1>
  <div class="hero-dots"><span></span><span></span><span></span><span class="on"></span></div>
</section>

<section class="abs welcome">
  <h2 class="section-title">WELCOME TO KELVANBROOK <span class="accent">DEVELOPMENT GROUP, INC</span></h2>
  <div class="rule"></div>
  <p>Kelvanbrook Development Group, Inc. was established in 1991. Our mission is helping businesses and individuals realize a Return on Investment by implementing today's advanced technologies. As a small business we understand the importance of technology and personalized attention. Every member of our support team has worked with both large and small companies supporting a multitude of applications, networks and environments.</p>
  <p>We interface daily with Clients and their customers to establish your support needs. A prerequisite for working with Kelvanbrook is having both the technological knowledge and the customer skills to communicate and work with customers to resolve technology issues. Whether it is a simple computer network, phone systems, or an advanced integrated infrastructure, we will study your requirements, suggest methodologies, and implement the design.</p>
</section>

<aside class="abs inquiry">
  <div class="inquiry-tab">Quick Inquiry</div>
  <div class="field" style="top:54px">First Name</div>
  <div class="field" style="top:96px">Email</div>
  <div class="field" style="top:138px">Phone</div>
  <div class="field tall" style="top:181px">Message</div>
  <div class="submit">Submit</div>
</aside>

<section class="abs services">
  <h2 class="section-title">OUR <span class="accent">SERVICES</span></h2>
  <div class="rule"></div>
  <div class="services-art" role="img" aria-label="Semicircle infographic of nine service icons arranged around the company name"></div>
  <div class="services-name">KELVANBROOK</div>
  <div class="svc-label" style="left:100px;top:473px;text-align:right;width:106px">DESKTOP<br>SUPPORT</div>
  <div class="svc-label" style="left:80px;top:353px;text-align:right;width:170px">NETWORK<br>ADMINISTRATION</div>
  <div class="svc-label" style="left:110px;top:258px;text-align:right;width:222px">TELECOMMUNICATIONS</div>
  <div class="svc-label" style="left:200px;top:184px;text-align:right;width:250px">AUDIO/VIDEO MULTIMEDIA</div>
  <div class="svc-label" style="left:485px;top:126px;text-align:center;width:230px">DISASTER RECOVERY</div>
  <div class="svc-label" style="left:783px;top:175px">WEB DESIGN</div>
  <div class="svc-label" style="left:899px;top:258px">NETWORK CABLING</div>
  <div class="svc-label" style="left:982px;top:353px">WIRELESS<br>NETWORKS</div>
  <div class="svc-label" style="left:1014px;top:462px">ANTIVIRUS<br>SOLUTIONS</div>
</section>

<section class="abs panel left">
  <h3 class="panel-title"><svg width="30" height="30" viewBox="0 0 30 30"><circle cx="15" cy="9" r="7" fill="#fff"/><path d="M3 29a12 10 0 0 1 24 0z" fill="#fff"/></svg>IT SUPPORT SOLUTIONS</h3>
  <div class="panel-rule" style="left:86px"></div>
  <div class="panel-photo" style="left:86px;background:linear-gradient(135deg,#2c4a66,#8fa9c0)" role="img" aria-label="Technicians working beside server racks in a data centre"></div>
  <p class="panel-text" style="left:310px">Lorem ipsum dolor sit amet, consectetuer adipiscing elit, sed diam nonummy nibh euismod tincidunt ut laoreet et dolore magna aliquam erat volutpat. Ut wisi minim consequat.</p>
  <div class="read-more">Read More &nbsp;⟶</div>
</section>
<section class="abs panel right">
  <h3 class="panel-title"><svg width="30" height="30" viewBox="0 0 30 30"><circle cx="15" cy="7" r="5" fill="#222"/><circle cx="5" cy="10" r="4" fill="#222"/><circle cx="25" cy="10" r="4" fill="#222"/><rect x="8" y="15" width="14" height="12" fill="#222"/></svg>WHY OUTSOURCE TECHNOLOGIES</h3>
  <div class="panel-rule" style="left:31px"></div>
  <div class="panel-photo" style="left:31px;background:radial-gradient(circle at 50% 45%,#6fc6f5,#0d2d55 70%)" role="img" aria-label="Hand holding a tablet with a glowing globe of digital content"></div>
  <p class="panel-text" style="left:253px">Lorem ipsum dolor sit amet, consectetuer adipiscing elit, sed diam nonummy nibh euismod tincidunt ut laoreet et dolore magna aliquam erat volutpat. Ut wisi minim consequat.</p>
  <div class="read-more">Read More &nbsp;⟶</div>
</section>
<div class="abs panel-notch"></div>

<section class="abs testimonials">
  <h2 class="section-title">CLIENTS <span class="accent">TESTIMONIALS</span></h2>
  <div class="rule"></div>
  <svg class="abs" style="left:115px;top:218px" width="24" height="54" viewBox="0 0 24 54"><path d="M22 2L2 27l20 25" fill="none" stroke="#bbb" stroke-width="2"/></svg>
  <svg class="abs" style="left:1060px;top:218px" width="24" height="54" viewBox="0 0 24 54"><path d="M2 2l20 25L2 52" fill="none" stroke="#bbb" stroke-width="2"/></svg>
  <p class="quote"><span class="mark">“</span> Lorem ipsum dolor sit amet, consectetuer adipiscing elit, sed diam nonummy nibh euismod tincidunt ut laoreet dolore magna aliquam erat volutpat. Ut wisi enim ad minim veniam, quis nostrud exercitorni mornkle tation ullamcorper suscipit lobortis nisl ut aliquip ex ea commodo consequat. <span class="mark">”</span></p>
  <div class="author">Lena R.<small>Brookdale, OR</small></div>
</section>

<section class="abs cta">
  <div class="cta-text">IT Solutions That Work For Your Business<span class="sub">A Full Service Technology Company</span></div>
  <div class="call-btn">
    <svg width="22" height="22" viewBox="0 0 24 24"><path fill="#fff" d="M6.6 10.8a15.1 15.1 0 0 0 6.6 6.6l2.2-2.2c.3-.3.7-.4 1-.2 1.1.4 2.3.6 3.6.6.6 0 1 .4 1 1V20c0 .6-.4 1-1 1A17 17 0 0 1 3 4c0-.6.4-1 1-1h3.5c.6 0 1 .4 1 1 0 1.3.2 2.5.6 3.6.1.3 0 .7-.2 1z"/></svg>
    <div>Call Us Today<br>(555) 014-2870</div>
  </div>
</section>

<footer class="abs footer" role="img" aria-label="Dark night-time city skyline behind the footer">
  <div class="footer-col" style="left:86px">
    <h4>Quick <span>Links</span></h4>
    <ul class="links"><li>Home</li><li>About Us</li><li>Services</li><li>Support</li><li>Clients</li><li>Careers</li><li>Contact Us</li></ul>
  </div>
  <div class="footer-col contact" style="left:318px">
    <h4>Contact <span>Details</span></h4>
    <ul>
      <li>Kelvanbrook Development Group, Inc.</li>
      <li class="addr">418 Marlow Ave.<br>Fairview, Ohio 40012</li>
      <li><svg width="12" height="12" viewBox="0 0 24 24"><path fill="#1b93dc" d="M6.6 10.8a15.1 15.1 0 0 0 6.6 6.6l2.2-2.2c.3-.3.7-.4 1-.2 1.1.4 2.3.6 3.6.6.6 0 1 .4 1 1V20c0 .6-.4 1-1 1A17 17 0 0 1 3 4c0-.6.4-1 1-1h3.5c.6 0 1 .4 1 1 0 1.3.2 2.5.6 3.6.1.3 0 .7-.2 1z"/></svg>(555) 014-2870</li>
      <li><svg width="12" height="12" viewBox="0 0 24 24"><rect x="3" y="8" width="18" height="10" fill="#1b93dc"/><rect x="7" y="3" width="10" height="6" fill="#1b93dc"/></svg>(555) 014-2871</li>
      <li><svg width="12" height="12" viewBox="0 0 24 24"><rect x="2" y="5" width="20" height="14" rx="2" fill="#1b93dc"/><path d="M2 6l10 7 10-7" stroke="#fff" fill="none" stroke-width="2"/></svg>info@kelvanbrook.com</li>
    </ul>
  </div>
  <div class="footer-col" style="left:654px">
    <h4>Get <span>Social</span></h4>
    <ul class="social-list">
      <li><span class="box"></span>Friendlane</li>
      <li><span class="box"></span>Chirpline</li>
      <li><span class="box"></span>Circlehub</li>
      <li><span class="box"></span>Workpath</li>
    </ul>
  </div>
</footer>

<div class="abs copyright">Copyright © 2017 Kelvanbrook Development Group, Inc. All Rights Reserved.</div>

</body>
</html>
```